Local fast-growing company in the service sector

We are looking for a modern business card design, which should also appear on our letterheads

Target Market(s)

Private and industrial sectors

Contact Information for Business Card

Vorname Name
Kellberger Str. 18
72816 Lindenhall
Tel.: 07146-839214-0
Name@agentur-kvtl.de

Colors
9d9d9d
919191
aaaaaa

Requirements
Must have
• The logo (file) in silver

```html
<!DOCTYPE html>
<html lang="de">
<head>
<meta charset="utf-8">
<title>KVTL – Visitenkarte</title>
<link rel="stylesheet" href="https://fonts.googleapis.com/css2?family=Montserrat:wght@400;500;700&family=Michroma&display=swap">
<style>
  :root {
    --backdrop: #3b3b3b;
    --card: #1d1d1f;
    --silver: #aaaaaa;
    --silver-mid: #9d9d9d;
    --silver-dark: #919191;
    --ink-light: #e6e6e6;
  }
  * { box-sizing: border-box; margin: 0; padding: 0; }
  html, body { width: 799px; height: 1200px; overflow: hidden; }
  body {
    background: var(--backdrop);
    font-family: "Montserrat", sans-serif;
    display: flex;
    flex-direction: column;
    align-items: center;
    justify-content: space-around;
    padding: 60px 0;
  }
  .card {
    position: relative;
    width: 620px;
    height: 400px;
    background: var(--card);
    border-radius: 4px;
    box-shadow: 0 14px 30px rgba(0,0,0,.45);
  }
  .card-front {
    display: flex;
    align-items: center;
    justify-content: center;
  }
  .front-wordmark {
    font-weight: 700;
    font-size: 96px;
    letter-spacing: 6px;
    color: var(--silver-dark);
  }
  .holder-name {
    position: absolute;
    top: 56px;
    left: 44px;
    font-family: "Michroma", sans-serif;
    font-weight: 400;
    font-size: 22px;
    letter-spacing: 3px;
    white-space: nowrap;
    color: var(--silver-mid);
    line-height: 1.2;
  }
  .contact {
    position: absolute;
    left: 44px;
    top: 200px;
    list-style: none;
    font-size: 14px;
    color: var(--ink-light);
    line-height: 1.6;
  }
  .contact li { display: flex; align-items: center; gap: 8px; }
  .contact .plain { padding-left: 21px; }
  .contact svg { width: 13px; height: 13px; fill: none; stroke: var(--ink-light); stroke-width: 1.6; flex: none; }
  .brand {
    position: absolute;
    right: 44px;
    bottom: 44px;
    display: flex;
    align-items: center;
    gap: 12px;
  }
  .brand-square { width: 40px; height: 40px; background: var(--silver); }
  .brand-name {
    font-weight: 700;
    font-size: 58px;
    letter-spacing: 2px;
    color: var(--silver);
    line-height: 1;
  }
</style>
</head>
<body>
  <section class="card card-front" aria-label="Vorderseite">
    <span class="front-wordmark">KVTL</span>
  </section>

  <section class="card card-back" aria-label="Rückseite">
    <h1 class="holder-name">VORNAME NAME</h1>
    <ul class="contact">
      <li class="plain">Kellberger Str. 18</li>
      <li class="plain">72816 Lindenhall</li>
      <li>
        <svg viewBox="0 0 16 16"><path d="M3 2h3l1.5 3.5-2 1.2a8 8 0 0 0 3.8 3.8l1.2-2L14 10v3a1 1 0 0 1-1 1A11 11 0 0 1 2 3a1 1 0 0 1 1-1z"/></svg>
        07146-839214-0
      </li>
      <li>
        <svg viewBox="0 0 16 16"><rect x="1.5" y="3.5" width="13" height="9"/><path d="M1.5 3.5 8 9l6.5-5.5"/></svg>
        Name@agentur-kvtl.de
      </li>
      <li>
        <svg viewBox="0 0 16 16"><circle cx="8" cy="8" r="6.5"/><path d="M1.5 8h13M8 1.5c-3 3.5-3 9.5 0 13M8 1.5c3 3.5 3 9.5 0 13"/></svg>
        www.agentur-kvtl.de
      </li>
    </ul>
    <div class="brand">
      <span class="brand-square"></span>
      <span class="brand-name">KVTL</span>
    </div>
  </section>
</body>
</html>
```